Business cards for KORU Real Estate Holdings LLC

We need a cool, original business card design for a company based in the Washington DC metropolitan area. We are a new energetic and passionate Real Estate Investing Company that invests in all types of real estate; commercial, residential, industrial etc.

Our company color is Red since it reflects action, energy and speed; it is assertive confident, energizing, exciting, powerful, passionate and determined. So we would like business card communicate those qualities to the audience.

Our audiences are investors that want to invest with us, real estate sellers, buyers, and tenants who lease from us.

Our logo is attached

```html
<!DOCTYPE html>
<html lang="en">
<head>
<meta charset="utf-8">
<title>KORU Real Estate Holdings LLC — Business Cards</title>
<link rel="stylesheet" href="https://fonts.googleapis.com/css2?family=Exo+2:wght@600;700&family=Open+Sans:wght@400;600&display=swap">
<style>
  :root {
    --page: #f3f3f3;
    --card-front: #ffffff;
    --card-back: #a7a8aa;
    --ink: #111111;
    --red: #d8232a;
    --back-mark: #8e8f91;
    --shadow: rgba(0, 0, 0, 0.18);
  }
  * { margin: 0; padding: 0; box-sizing: border-box; }
  html, body {
    width: 1200px;
    height: 873px;
    overflow: hidden;
    background: var(--page);
  }
  .sheet {
    width: 1200px;
    height: 873px;
    display: flex;
    align-items: center;
    justify-content: center;
    gap: 60px;
  }
  .card {
    width: 520px;
    height: 298px;
    border-radius: 4px;
    box-shadow: 0 10px 28px var(--shadow);
    position: relative;
    overflow: hidden;
  }
  .card--front { background: var(--card-front); }
  .card--back  { background: var(--card-back); }

  .brand {
    position: absolute;
    left: 44px;
    top: 40px;
    display: flex;
    align-items: center;
    gap: 16px;
  }
  .brand__dot {
    width: 40px;
    height: 40px;
    border-radius: 50%;
    background: var(--red);
  }
  .brand__name {
    font-family: "Exo 2", sans-serif;
    font-weight: 700;
    font-size: 84px;
    line-height: 1;
    letter-spacing: 6px;
    color: var(--ink);
  }
  .brand__tagline {
    position: absolute;
    left: 100px;
    top: 132px;
    font-family: "Open Sans", sans-serif;
    font-weight: 600;
    font-size: 15px;
    letter-spacing: 1px;
    text-transform: uppercase;
    color: var(--ink);
  }
  .contact {
    position: absolute;
    left: 44px;
    bottom: 36px;
    display: grid;
    grid-template-columns: auto auto;
    column-gap: 12px;
    row-gap: 4px;
    align-items: baseline;
  }
  .contact__label {
    font-family: "Exo 2", sans-serif;
    font-weight: 700;
    font-size: 14px;
    text-transform: uppercase;
    text-align: right;
    color: var(--red);
  }
  .contact__value {
    font-family: "Open Sans", sans-serif;
    font-weight: 400;
    font-size: 15px;
    color: var(--ink);
  }

  .back-mark {
    position: absolute;
    inset: 0;
    display: flex;
    align-items: center;
    justify-content: center;
    font-family: "Exo 2", sans-serif;
    font-weight: 700;
    font-size: 120px;
    letter-spacing: 12px;
    color: var(--back-mark);
  }
</style>
</head>
<body>
  <main class="sheet">
    <section class="card card--front" aria-label="Business card front">
      <div class="brand">
        <span class="brand__dot"></span>
        <span class="brand__name">KORU</span>
      </div>
      <p class="brand__tagline">Real Estate Holdings LLC</p>
      <dl class="contact">
        <dt class="contact__label">Phone:</dt>
        <dd class="contact__value">202-555-0148</dd>
        <dt class="contact__label">Web:</dt>
        <dd class="contact__value">koruholdings.com</dd>
        <dt class="contact__label">Email:</dt>
        <dd class="contact__value">jane.reed@koruholdings.com</dd>
      </dl>
    </section>

    <section class="card card--back" aria-label="Business card back">
      <div class="back-mark">KORU</div>
    </section>
  </main>
</body>
</html>
```